Accountant website

Please design a accountant website for www.fenwaybridgeadvisory.com.au. This site is majorly out of date, and is not supported by modern browsers.

The style should use the reds from the design at dev.fenwaybridgeadvisory.com.au, and should be modern and make use of Slides (large content slides that the user scrolls through on the front page).

The content is largely already on the site, however happy to move some around to suit the modern design as required.

The dev.fenwaybridgeadvisory.com.au was a rough mock up that I have completed that the client is "happy" with the direction, however this needs a lot of polish and finishing touches, and I will accept designs that differ from this, but highly recommend that this is used as a guide.

Ready to be sliced PSD Only - HTML no required.

In all honesty, although I can technically do a lot of this, the polished finished I want for this site has eluded me in a few attempts, and therefore I am looking out there at you much more artistic people to finish (or redesign if required) this site.

Target Market(s)

Higher end Small - Medium Business

Industry/Entity Type

Accountant

Requirements
Must have
• Must use the logo from dev.fenwaybridgeadvisory.com.au use exactly the red colours as defined in this layout. A basic layout PSD (to get the colour etc) and the logo in ai format is attached to this project. Please ignore the SSL warning on the development site.

The final product does NOT have to be the same as shown on dev.fenwaybridgeadvisory.com.au however the red colour scheme must be used. The client DOES want the logo on the RIGHT.

Must have a front landing page design, and a page layout that considers the other page content (at least one separate PSD)
Nice to have
• I really am looking at a slide format for the front page simular to:

http://www.quillo.com/au/
http://www.vaultmoor.com/

The attached photos should be used on the site. Was considering a rotating banner with these images are a watermark background on a solid Red header bar, but happy to be shown other options.
Should not have
• Please no "Layout Goblin" submissions.

```html
<!DOCTYPE html>
<html lang="en">
<head>
<meta charset="utf-8">
<title>Fenway Bridge Advisory</title>
<link href="https://fonts.googleapis.com/css2?family=Source+Sans+3:wght@300;400;600;700&family=Roboto+Condensed:wght@400;700&display=swap" rel="stylesheet">
<style>
:root{
  --red:#a62a2a;
  --red-dark:#8c1f1f;
  --red-light:#c23a3a;
  --ink:#333;
  --muted:#666;
  --line:#e2e2e2;
  --panel:#f3f3f3;
  --footer:#2d2d2d;
  --footer-dark:#232323;
}
*{box-sizing:border-box;margin:0;padding:0}
html,body{width:698px;height:1200px;overflow:hidden;background:#fff}
body{position:relative;font-family:"Source Sans 3",Arial,sans-serif;color:var(--ink)}
.abs{position:absolute}
.topline{left:0;top:0;width:698px;height:3px;background:#9a9a9a}
.header{left:0;top:3px;width:698px;height:73px;background:linear-gradient(#fff,#f2f2f2)}
.brand{right:73px;top:20px;display:flex;align-items:center;gap:6px}
.brand-name{font-weight:700;font-size:19px;color:#222;line-height:1}
.brand-sub{font-size:7.5px;color:#333;letter-spacing:.3px;margin-top:2px}
.brand-mark{width:14px;height:14px;background:var(--red)}
.nav{left:0;top:76px;width:698px;height:28px;background:linear-gradient(var(--red-light),var(--red-dark));border-bottom:1px solid #6d1616}
.nav ul,.footer-nav ul{list-style:none;display:flex;position:absolute;left:70px;top:0;height:100%;align-items:center}
.nav li,.footer-nav li{font-family:"Roboto Condensed",sans-serif;font-size:9.5px;color:#fff;margin-right:23px;text-transform:uppercase}
.nav li.active{background:var(--red-dark);border:1px solid #5e1010;padding:3px 5px;margin-left:-6px}
.hero{left:0;top:104px;width:698px;height:241px;background:radial-gradient(circle at 50% 40%,#f4f1ea 0%,#ddd6cc 55%,#c9c1bb 100%)}
.arrow{width:25px;height:25px;border-radius:50%;background:#f4f4f4;border:1px solid #ccc;top:211px}
.arrow svg{position:absolute;left:8px;top:7px}
.caption{left:58px;top:310px;width:583px;height:35px;background:rgba(245,245,245,.9);display:flex;align-items:center;justify-content:center;gap:12px}
.caption p{font-family:"Roboto Condensed",sans-serif;font-size:15px;color:#222}
.btn{background:#3a3a3a;color:#fff;font-family:"Roboto Condensed",sans-serif;font-size:10.5px;padding:5px 8px;border-radius:2px;border:1px solid #222}
.feature{top:357px;width:200px;text-align:center}
.feature h3{font-family:"Roboto Condensed",sans-serif;font-weight:700;font-size:10.5px;color:var(--red);line-height:16px;margin-top:10px}
.rule{left:58px;width:583px;height:1px;background:var(--line)}
.intro{left:80px;top:458px;width:538px;text-align:center}
.intro h1{font-weight:300;font-size:18.5px;color:#333}
.intro p{font-size:8px;line-height:14.5px;color:var(--muted);margin-top:8px}
.photo{border:3px solid #ccc}
.principal{left:259px;top:556px;width:377px}
.principal h2,.team h2{font-weight:300;font-size:17.5px;color:var(--red)}
.principal p,.team p{font-size:7px;line-height:12px;color:var(--muted);margin-top:6px;text-align:justify}
.more{color:var(--red);font-weight:600}
.team{left:62px;top:714px;width:380px}
.avatar{top:718px;width:58px;height:58px;border-radius:50%;border:2px solid #ddd}
.tabs{left:65px;top:843px;list-style:none}
.tabs li{font-size:10px;color:#333;height:30.5px}
.tabs li.active{color:var(--red)}
.tabs li::before{content:"»";margin-right:6px}
.panel{left:245px;top:839px;width:396px;height:114px;background:var(--panel);border-left:1px solid var(--line);padding:14px 14px}
.panel h4{font-weight:400;font-size:10.5px;color:#222}
.panel p{font-size:7.5px;line-height:16px;color:var(--muted);margin-top:6px}
.newsband{left:0;top:980px;width:698px;height:70px;background:#f3f3f3;border-top:1px solid var(--line);border-bottom:1px solid var(--line)}
.news-label{left:70px;top:1014px;width:62px;text-align:center;font-size:11px;color:var(--red);font-weight:600}
.news-div{left:145px;top:985px;width:1px;height:60px;background:#ccc}
.news-text{left:159px;top:995px;width:470px;font-size:7.5px;line-height:12px;color:#555}
.news-date{color:#222;margin-top:5px}
.partners{left:62px;top:1068px;width:580px;display:flex;justify-content:space-between;align-items:center}
.partners span{font-size:12px;color:#555;font-weight:600}
.footer{left:0;top:1106px;width:698px;height:94px;background:linear-gradient(var(--footer),var(--footer-dark))}
.footer-nav{left:0;top:1106px;width:698px;height:38px}
.footer-nav li{color:#ddd}
.footer-rule{left:58px;top:1144px;width:583px;height:1px;background:#444}
.copy{left:58px;top:1156px;font-size:7.5px;color:#aaa;line-height:19px}
.badge{left:489px;top:1160px;display:flex;align-items:center;gap:8px}
.badge-seal{width:24px;height:24px;border-radius:50%;background:#c33;border:2px solid #eee}
.badge-text{font-size:7.5px;color:#ddd;line-height:9px;font-weight:600}
.foot-brand{left:580px;top:1162px;font-size:11px;font-weight:700;color:#999}
</style>
</head>
<body>
<div class="abs topline"></div>
<header class="abs header"></header>
<div class="abs brand">
  <div>
    <div class="brand-name">FENWAY BRIDGE</div>
    <div class="brand-sub">ADVISORY</div>
  </div>
  <div class="brand-mark"></div>
</div>

<nav class="abs nav">
  <ul>
    <li class="active">Home</li><li>About Us</li><li>Services</li><li>Working With Us</li><li>Contact Us</li><li>Links</li><li>Testimonials</li><li>News</li><li>Articles</li>
  </ul>
</nav>

<div class="abs hero" role="img" aria-label="Stressed office worker holding his head, surrounded by scattered paperwork"></div>
<div class="abs arrow" style="left:57px"><svg width="8" height="10"><path d="M6 1L2 5l4 4" stroke="#999" stroke-width="1.3" fill="none"/></svg></div>
<div class="abs arrow" style="left:615px"><svg width="8" height="10"><path d="M2 1l4 4-4 4" stroke="#999" stroke-width="1.3" fill="none"/></svg></div>
<div class="abs caption">
  <p>Too musch bookkeeping let us take the load off</p>
  <span class="btn">CONTACT US &rsaquo;</span>
</div>

<div class="abs feature" style="left:55px">
  <svg width="22" height="26" viewBox="0 0 22 26"><path d="M7 2a2 2 0 0 1 4 0v9h1V9a2 2 0 0 1 4 0v3a2 2 0 0 1 4 0v7c0 4-3 6-6 6H10c-3 0-5-3-6-5L1 14a2 2 0 0 1 3-2l3 3z" fill="var(--red)"/></svg>
  <h3>BUSINESS ESTABLISHMENT</h3>
</div>
<div class="abs feature" style="left:249px">
  <svg width="30" height="26" viewBox="0 0 30 26"><rect x="2" y="18" width="4" height="7" fill="var(--red)"/><rect x="8" y="14" width="4" height="11" fill="var(--red)"/><rect x="14" y="16" width="4" height="9" fill="var(--red)"/><rect x="20" y="10" width="4" height="15" fill="var(--red)"/><path d="M2 14l7-6 5 3 11-9" stroke="var(--red)" stroke-width="2" fill="none"/><path d="M22 2h5v5" stroke="var(--red)" stroke-width="2" fill="none"/></svg>
  <h3>MANAGEMENT DURING BUSINESS<br>GROWTH &amp; MATURITY</h3>
</div>
<div class="abs feature" style="left:443px">
  <svg width="28" height="28" viewBox="0 0 28 28"><circle cx="14" cy="13" r="5.5" stroke="var(--red)" stroke-width="2" fill="none"/><rect x="11.5" y="19" width="5" height="5" fill="var(--red)"/><path d="M14 1v3M4 4l2 2M24 4l-2 2M1 13h3M24 13h3" stroke="var(--red)" stroke-width="1.6"/></svg>
  <h3>BUSINESS CESSATION</h3>
</div>

<div class="abs rule" style="top:441px"></div>

<section class="abs intro">
  <h1>Building a Relationship with Fenway Bridge Advisory</h1>
  <p>Fenway Bridge Advisory believes that people choose to do business with people, not companies. As a result we provided a brief overview of our service process so that you know what to expect when you meet with Fenway Bridge Advisory. We also take this opportunity to introduce you to our team.</p>
</section>

<div class="abs photo" style="left:64px;top:561px;width:181px;height:104px;background:linear-gradient(90deg,#b9c3cc,#d8d2cc 55%,#a7524f 62%,#c9c2b8)" role="img" aria-label="The principal standing at a marina with boats behind her"></div>
<section class="abs principal">
  <h2>The Principal &ndash; Helena Marsh</h2>
  <p>Helena achieved her Bachelor of Commerce degree from the University of Hartwell in 2001 and went on to complete her Chartered Accountant qualifications. She has been a member of the Institute of Certified Accountants since May 2005.</p>
  <p>With over 11 years experience in the accounting profession, working with high profile businesses within the Hartwell area, Helena has developed a great understanding of the varying needs of different businesses within their industries. <span class="more">MORE</span></p>
</section>

<div class="abs rule" style="top:690px"></div>

<section class="abs team">
  <h2>The Team</h2>
  <p>Helena is supported by a team of 3 staff who understand the importance of developing and maintaining client relationships. The team are dedicated to providing you with the best possible service which exceeds your expectations.<br><span class="more">MEET THE TEAM...</span></p>
</section>
<div class="abs avatar" style="left:454px;background:linear-gradient(#8ea1b3,#6d7f8f)" role="img" aria-label="Team member portrait"></div>
<div class="abs avatar" style="left:515px;background:linear-gradient(#9fb3c6,#4f7fc0)" role="img" aria-label="Team member portrait"></div>
<div class="abs avatar" style="left:576px;background:linear-gradient(#a9b5c0,#e8e4df)" role="img" aria-label="Team member portrait"></div>

<div class="abs rule" style="top:816px"></div>

<ul class="abs tabs">
  <li class="active">Complimentary Client Consultation</li>
  <li>Customised Accounting Solution</li>
  <li>Quote Acceptance</li>
  <li>Ongoing Business Advice</li>
</ul>
<div class="abs panel">
  <h4>Complimentary Client Consultation</h4>
  <p>MeetingA one-hour meeting is held at a mutually convenient time to enable us to learn about you and your business. Throughout which the focus is on your business. We discuss the challenges you face in your business, and brainstorm how we can assist you with overcoming these challenges. We also discuss your goals and the future direction you want your business to take.</p>
</div>

<div class="abs newsband"></div>
<svg class="abs" style="left:92px;top:997px" width="20" height="16" viewBox="0 0 20 16"><rect x="1" y="1" width="18" height="14" fill="none" stroke="var(--red)" stroke-width="2"/><rect x="4" y="4" width="5" height="4" fill="var(--red)"/><path d="M11 5h5M11 8h5M4 11h12" stroke="var(--red)" stroke-width="1.4"/></svg>
<div class="abs news-label">Latest News</div>
<div class="abs news-div"></div>
<div class="abs news-text">
  <p>Nulla condimentum orci vitae augue rutrum venenatis. Sed erat leo, varius id magna sit amet, pellentesque eleifend ligula. Nulla non massa id neque lobortis vestibulum.</p>
  <p class="news-date">October 12 - 2013</p>
</div>

<div class="abs partners">
  <span>Greenbay</span><span>Lumora</span><span>Netlace</span><span>Quarto</span><span>Halvex</span><span>QT</span><span>Brightsoft</span><span>Adelo</span><span>Norvan</span>
</div>

<footer class="abs footer"></footer>
<nav class="abs footer-nav">
  <ul><li>Home</li><li>About Us</li><li>Services</li><li>Working With Us</li><li>Contact Us</li><li>Links</li><li>Testimonials</li><li>News</li><li>Articles</li></ul>
</nav>
<div class="abs footer-rule"></div>
<div class="abs copy">Copyright &copy; 2013 &nbsp;fenwaybridgeadvisory.com.au<br>All rights reserved</div>
<div class="abs badge"><div class="badge-seal"></div><div class="badge-text">Certified<br>Accountants</div></div>
<div class="abs foot-brand">FENWAY BRIDGE</div>
</body>
</html>
```